U.S. Popcorn company needs business cards

We are a popcorn company that manufactures popcorn and sells it to grocery stores worldwide. Our theme is "Americana" and our logo is U.S. route 66 which is the most famous highway in the U.S.

We would like the design to be simple and to use both sides. On the back side we would like to see just the logo and website. The front would be normal details

Target Market(s)

Wholesalers, grocers and distributors

Industry/Entity Type

Manufacture

Contact Information for Business Card

Business name: Prairie Lantern Popcorn
Phone: +1 555 308 4726
Email: Dale@prairielanternpopcorn.com
website: www.prairielanternpopcorn.com
Tag Line: "POPular for a reason"
Name: Dale Whitcombe
Title: Founder/President

Requirements
Must have
• Either this design should be fun or clean and simple. I will let you show me your thougths.
Nice to have
• Anything that ties in the real Hwy Route 66.
• Colors might need to be red, white and blue incorporated.
Should not have
• Not be too busy.

```html
<!DOCTYPE html>
<html lang="en">
<head>
<meta charset="utf-8">
<title>Prairie Lantern Popcorn – Business Card</title>
<link rel="stylesheet" href="https://fonts.googleapis.com/css2?family=Lato:wght@400;700&family=Raleway:wght@700&family=Patrick+Hand&display=swap">
<style>
  :root {
    --page-bg: #ececec;
    --card-bg: #363636;
    --card-bg-light: #404040;
    --card-bg-dark: #2c2c2c;
    --accent-red: #e31e24;
    --text-white: #ffffff;
    --text-soft: #e6e6e6;
  }
  * { margin: 0; padding: 0; box-sizing: border-box; }
  html, body {
    width: 1200px; height: 586px; overflow: hidden;
    background: var(--page-bg);
  }
  .canvas {
    position: relative; width: 1200px; height: 586px;
  }
  .card {
    position: absolute; top: 143px;
    width: 502px; height: 300px;
    overflow: hidden;
  }
  .card--back { left: 61px; }
  .card--front { left: 619px; }
  .card__texture {
    position: absolute; inset: 0;
    background: linear-gradient(135deg, var(--card-bg-light) 0%, var(--card-bg) 45%, var(--card-bg-dark) 100%);
  }
  .brand {
    position: absolute; left: 0; right: 0; top: 112px;
    display: flex; align-items: center; justify-content: center; gap: 10px;
  }
  .brand__dot {
    width: 16px; height: 16px; border-radius: 50%;
    background: var(--accent-red);
  }
  .brand__name {
    font-family: 'Lato', sans-serif; font-weight: 700;
    font-size: 26px; color: var(--text-white);
  }
  .tagline {
    position: absolute; left: 0; right: 0; top: 250px;
    text-align: center;
    font-family: 'Patrick Hand', cursive;
    font-size: 14px; letter-spacing: 2.5px;
    color: var(--text-white);
  }
  .person {
    position: absolute; right: 300px; top: 133px;
    text-align: right;
  }
  .person__name {
    font-family: 'Raleway', sans-serif; font-weight: 700;
    font-size: 16px; color: var(--accent-red);
  }
  .person__title {
    margin-top: 2px;
    font-family: 'Lato', sans-serif; font-weight: 400;
    font-size: 11.5px; color: var(--text-soft);
  }
  .divider {
    position: absolute; left: 215px; top: 88px;
    width: 2px; height: 128px;
    background: linear-gradient(to bottom, rgba(255,255,255,0), rgba(255,255,255,0.85) 50%, rgba(255,255,255,0));
  }
  .contact {
    position: absolute; left: 250px; top: 120px;
    list-style: none;
    font-family: 'Lato', sans-serif; font-weight: 700;
    font-size: 12px; color: var(--text-white);
  }
  .contact__item {
    display: flex; align-items: center; gap: 9px;
    height: 16px; margin-bottom: 8px;
  }
  .contact__icon { width: 12px; height: 12px; fill: var(--accent-red); }
  .contact__item--web { color: var(--accent-red); }
</style>
</head>
<body>
<main class="canvas">
  <section class="card card--back">
    <div class="card__texture" role="img" aria-label="Dark charcoal low-poly geometric background"></div>
    <div class="brand">
      <span class="brand__dot"></span>
      <span class="brand__name">Prairie Lantern Popcorn</span>
    </div>
    <p class="tagline">POPular for a reason</p>
  </section>

  <section class="card card--front">
    <div class="card__texture" role="img" aria-label="Dark charcoal low-poly geometric background"></div>
    <div class="person">
      <p class="person__name">Dale Whitcombe</p>
      <p class="person__title">Founder/President</p>
    </div>
    <div class="divider"></div>
    <ul class="contact">
      <li class="contact__item">
        <svg class="contact__icon" viewBox="0 0 24 24" aria-hidden="true"><path d="M3 9c0-3 4-5 9-5s9 2 9 5v2h-5V8.5c-1-.5-2.5-.8-4-.8s-3 .3-4 .8V11H3zM6 12l3-3h6l3 3 2 8H4zm6 2.5a2.5 2.5 0 1 0 0 5 2.5 2.5 0 0 0 0-5z"/></svg>
        <span>+1 555 308 4726</span>
      </li>
      <li class="contact__item">
        <svg class="contact__icon" viewBox="0 0 24 24" aria-hidden="true"><path d="M2 5h20v14H2zm2 2v.5l8 5.5 8-5.5V7zm0 3v7h16v-7l-8 5.5z"/></svg>
        <span>Dale@prairielanternpopcorn.com</span>
      </li>
      <li class="contact__item contact__item--web">
        <span>www.prairielanternpopcorn.com</span>
      </li>
    </ul>
  </section>
</main>
</body>
</html>
```